Yard sign

Looking for a yard sign. <br/>Something simple, name, number. <br/>Large text, readable from 50 feet away. <br/><br/>18 x 24 inches.

Target Market(s)

Potential homeowners thinking about going solar.

Colors

Designer to choose colors to be used in the design.

Requirements
Must have
• "WE'VE GONE SOLAR!"
Nice to have
• We are a solar company, we would like a design that compliments the homeowners decision that they went solar and encourages others to do the same.

```html
<!DOCTYPE html>
<html lang="en">
<head>
<meta charset="utf-8">
<title>We've Gone Solar – Yard Sign Options</title>
<link rel="stylesheet" href="https://fonts.googleapis.com/css2?family=Jost:wght@600;700&display=swap">
<style>
  :root {
    --board: #181b1c;
    --sign-white: #ffffff;
    --sun-orange: #fb7a0c;
    --label: #ffffff;
  }
  html, body {
    margin: 0;
    padding: 0;
    width: 1200px;
    height: 771px;
    overflow: hidden;
    background: var(--board);
  }
  .sheet { display: block; width: 1200px; height: 771px; }
  .sign-face { fill: var(--sign-white); }
  .sign-band { fill: var(--sun-orange); }
  .headline { fill: var(--sun-orange); font-family: "Jost", sans-serif; font-weight: 700; }
  .sun-placeholder { fill: var(--sun-orange); }
  .contact { fill: var(--sign-white); font-family: "Jost", sans-serif; font-weight: 700; }
  .brand-dot { fill: var(--sign-white); }
  .option-label { fill: var(--label); font-family: "Jost", sans-serif; font-weight: 700; font-size: 28px; text-anchor: middle; }
</style>
</head>
<body>
<svg class="sheet" viewBox="0 0 1200 771" xmlns="http://www.w3.org/2000/svg" role="img" aria-label="Five yard sign layout options reading We've Gone Solar">
  <defs>
    <symbol id="headline-block" viewBox="0 0 365 274" width="365" height="274" overflow="visible">
      <text class="headline" x="36" y="64" font-size="52" textLength="292" lengthAdjust="spacingAndGlyphs">WE'VE GONE</text>
      <text class="headline" x="35" y="139" font-size="96" textLength="42" lengthAdjust="spacingAndGlyphs">S</text>
      <circle class="sun-placeholder" cx="120" cy="109" r="36" role="img" aria-label="Sunburst illustration forming the letter O"/>
      <text class="headline" x="158" y="139" font-size="96" textLength="172" lengthAdjust="spacingAndGlyphs">LAR!</text>
    </symbol>

    <symbol id="contact-block" viewBox="0 0 365 274" width="365" height="274" overflow="visible">
      <circle class="brand-dot" cx="41" cy="210" r="8"/>
      <text class="contact" x="54" y="215" font-size="14" textLength="72" lengthAdjust="spacingAndGlyphs">Kestrel Solar</text>
      <text class="contact" x="138" y="218" font-size="34" textLength="192" lengthAdjust="spacingAndGlyphs">555-018-2740</text>
      <text class="contact" x="140" y="234" font-size="13" textLength="161" lengthAdjust="spacingAndGlyphs">www.kestrelsolar.com</text>
    </symbol>
  </defs>

  <g class="sign" transform="translate(37 44)">
    <rect class="sign-face" width="365" height="274"/>
    <path class="sign-band" d="M0 148 Q167 186 365 140 L365 274 L0 274 Z"/>
    <use href="#headline-block"/>
    <use href="#contact-block"/>
  </g>

  <g class="sign" transform="translate(417 44)">
    <rect class="sign-face" width="365" height="274"/>
    <path class="sign-band" d="M0 144 Q182 202 365 145 L365 274 L0 274 Z"/>
    <use href="#headline-block"/>
    <use href="#contact-block" y="3"/>
  </g>

  <g class="sign" transform="translate(797 44)">
    <rect class="sign-face" width="365" height="274"/>
    <path class="sign-band" d="M0 131 Q182 215 365 131 L365 274 L0 274 Z"/>
    <use href="#headline-block"/>
    <use href="#contact-block" y="3"/>
  </g>

  <g class="sign" transform="translate(188 413)">
    <rect class="sign-face" width="365" height="274"/>
    <path class="sign-band" d="M0 134 Q230 218 365 171 L365 274 L0 274 Z"/>
    <use href="#headline-block"/>
    <use href="#contact-block" y="3"/>
  </g>

  <g class="sign" transform="translate(593 413)">
    <rect class="sign-face" width="365" height="274"/>
    <path class="sign-band" d="M0 149 Q170 206 365 136 L365 274 L0 274 Z"/>
    <use href="#headline-block"/>
    <use href="#contact-block" y="3"/>
  </g>

  <text class="option-label" x="226" y="358">1</text>
  <text class="option-label" x="593" y="358">2</text>
  <text class="option-label" x="1029" y="358">3</text>
  <text class="option-label" x="361" y="729">4</text>
  <text class="option-label" x="783" y="729">5</text>
</svg>
</body>
</html>
```